Tech Company New PowerPoint Design Project

We are an IT Managed services, cloud and cyber security company https://www.travolin.com.au/ Requesting proposals for a PowerPoint deck template that can be used by our sales team when pitching clients, our head office is located in Australa and we do have regional offices in NZ , USA , SRI LANKA and SINGAPORE. and also required to have a proposal/SOW template created too (not sure if this is something that we can include to this proposal) we may need a lot of things done in future but this is where i like to get started for now.. please let m eknow your thoughts and if you have any questions.
Target Market(s)
Enterprise
Industry/Entity Type
Information Technology
Look and feel

```html
<!DOCTYPE html>
<html lang="en">
<head>
<meta charset="utf-8">
<title>Travolin Sales Deck Template</title>
<link href="https://fonts.googleapis.com/css2?family=Barlow:wght@400;500;600;700&family=Poppins:wght@300;400;500;600&display=swap" rel="stylesheet">
<style>
  :root{
    --blue:#0a8fd8;
    --blue-dark:#0b6fb8;
    --sky:#6ccbef;
    --navy:#1d3c6a;
    --ink:#222831;
    --grey:#5e646c;
    --muted:#8a9098;
    --rule:#c9ced4;
    --paper:#ffffff;
    --soft:#f3f5f7;
    --badge:#dfe4ea;
  }
  *{box-sizing:border-box;margin:0;padding:0}
  html,body{width:1200px;height:1101px;overflow:hidden;background:#fff}
  body{position:relative;font-family:"Poppins",sans-serif;color:var(--ink)}
  .slide{position:absolute;width:514px;height:288px;background:var(--paper);overflow:hidden;box-shadow:0 4px 14px rgba(0,0,0,.12)}
  .slide--cover{left:71px;top:64px}
  .slide--agenda{left:623px;top:64px}
  .slide--about{left:71px;top:398px}
  .slide--services{left:623px;top:398px;background:var(--soft)}
  .slide--partners{left:71px;top:733px;background:var(--soft)}
  .slide--contact{left:623px;top:733px;background:linear-gradient(135deg,#f7f8fa,#eceff2)}
  .abs{position:absolute}
  .photo{position:absolute}
  .heading{font-family:"Barlow",sans-serif;font-weight:500;color:var(--ink)}
  .heading-rule{position:absolute;height:2px;width:68px;background:var(--blue-dark)}
  .copyright{position:absolute;left:8px;bottom:10px;font-size:5.2px;font-weight:500;color:var(--ink)}
  .page-no{position:absolute;right:8px;bottom:10px;font-size:5.2px;color:var(--ink)}
  .foot-bar{position:absolute;left:0;bottom:0;width:100%;height:5px;background:linear-gradient(90deg,var(--blue-dark) 50%,var(--navy) 50%)}
  .wordmark{font-family:"Poppins",sans-serif;font-weight:300;color:var(--blue);letter-spacing:1px}

  /* cover */
  .cover-brand{left:388px;top:72px;font-size:29px;width:112px;text-align:center}
  .cover-tag{left:365px;top:110px;width:140px;text-align:center;font-size:9.4px;line-height:15.3px;color:var(--ink)}
  .cover-call{left:365px;top:197px;width:140px;text-align:center;font-size:13px;font-style:italic;font-weight:300}
  .cover-phone{left:360px;top:216px;width:150px;text-align:center;font-family:"Barlow",sans-serif;font-weight:700;font-size:22px;color:var(--ink)}

  /* agenda */
  .agenda-title{left:47px;top:128px;font-size:20px}
  .agenda-list{position:absolute;left:287px;top:58px;width:212px;list-style:none}
  .agenda-item{position:relative;height:37.6px}
  .agenda-pill{position:absolute;left:0;top:0;width:31px;height:20px;background:var(--blue-dark);border-radius:0 10px 10px 0}
  .agenda-label{position:absolute;left:44px;top:2px;font-family:"Barlow",sans-serif;font-weight:600;font-size:10.5px}
  .agenda-rule{position:absolute;left:21px;top:27px;width:186px;height:1px;background:var(--rule)}
  .agenda-bar{position:absolute;left:293px;bottom:0;width:182px;height:5px;background:var(--blue-dark)}

  /* about */
  .about-photo{left:19px;top:17px;width:199px;height:237px;border:2px solid var(--blue-dark)}
  .about-title{left:232px;top:16px;font-size:17.5px}
  .about-lead{left:232px;top:46px;width:234px;font-size:6.6px;line-height:12px;font-weight:500;text-align:justify}
  .about-body{left:247px;top:127px;width:234px;font-size:6.6px;line-height:12px;text-align:justify;color:#333}
  .about-body p{margin-bottom:7px}

  /* services */
  .services-title{left:0;width:514px;text-align:center;top:20px;font-size:17.5px}
  .svc-name{font-family:"Barlow",sans-serif;font-size:8.6px;font-weight:500;line-height:9.6px}
  .svc-desc{font-size:4.6px;line-height:8.4px;color:#555}
  .svc-left{position:absolute;left:2px;width:82px;text-align:right}
  .svc-right{position:absolute;left:418px;width:94px;text-align:left}
  .svc-right .svc-name{border-bottom:1px solid var(--blue);padding-bottom:2px;margin-bottom:4px;display:inline-block;width:70px}
  .svc-left .svc-name{margin-bottom:4px}
  .svc-ai{left:120px;top:232px;width:274px;text-align:center}

  /* partners */
  .partners-title{left:0;width:514px;text-align:center;top:20px;font-size:17.5px}
  .badge{position:absolute;height:16px;border-radius:3px;background:var(--badge)}

  /* contact */
  .contact-brand{left:30px;top:20px;font-size:40px;letter-spacing:2px}
  .contact-thanks{left:33px;top:72px;font-family:"Barlow",sans-serif;font-weight:600;font-size:18px;color:var(--grey)}
  .contact-line{left:35px;display:flex;align-items:center;gap:6px;font-size:10.6px}
  .office-head{display:flex;align-items:center;gap:6px;font-family:"Barlow",sans-serif;font-size:10px;font-weight:500}
  .office-body{margin-left:20px;margin-top:6px;font-size:7px;line-height:10.6px;color:#333}
</style>
</head>
<body>

<!-- Cover -->
<section class="slide slide--cover">
  <svg class="abs" width="514" height="288" viewBox="0 0 514 288">
    <defs>
      <linearGradient id="coverPhoto" x1="0" y1="0" x2="1" y2="1">
        <stop offset="0" stop-color="#2a2b30"/><stop offset=".55" stop-color="#4b5058"/><stop offset="1" stop-color="#1e2228"/>
      </linearGradient>
    </defs>
    <rect width="514" height="288" fill="url(#coverPhoto)" role="img" aria-label="Photo of a businessman in a suit working on a laptop with digital network graphics"/>
    <polygon points="397,0 514,0 514,288 385,288 268,162" fill="#fff"/>
    <polygon points="293,0 397,0 268,162 202,164" fill="var(--blue)"/>
    <polygon points="202,164 268,162 385,288 276,288" fill="var(--sky)"/>
  </svg>
  <div class="abs wordmark cover-brand">travolin</div>
  <p class="abs cover-tag">Ensuring your requirements are met in order to strengthen &amp; enhance your business to a whole new level</p>
  <div class="abs cover-call">CALL</div>
  <div class="abs cover-phone">02 8123 4567</div>
</section>

<!-- Agenda -->
<section class="slide slide--agenda">
  <span class="heading-rule" style="left:39px;top:121px"></span>
  <h2 class="abs heading agenda-title">Agenda</h2>
  <div class="photo" style="left:134px;top:0;width:159px;height:288px;background:linear-gradient(160deg,#3a5a78,#8fa9bd 55%,#56718a)" role="img" aria-label="Photo of a young woman working on a laptop with coding icons around her"></div>
  <ul class="agenda-list">
    <li class="agenda-item"><span class="agenda-pill"></span><span class="agenda-label">Introduction</span><span class="agenda-rule"></span></li>
    <li class="agenda-item"><span class="agenda-pill"></span><span class="agenda-label">About Us</span><span class="agenda-rule"></span></li>
    <li class="agenda-item"><span class="agenda-pill"></span><span class="agenda-label">Our Services</span><span class="agenda-rule"></span></li>
    <li class="agenda-item"><span class="agenda-pill"></span><span class="agenda-label">Our Partners</span><span class="agenda-rule"></span></li>
    <li class="agenda-item"><span class="agenda-pill"></span><span class="agenda-label">Contact</span><span class="agenda-rule"></span></li>
  </ul>
  <span class="copyright">Copyright 2024. All rights reserved.</span>
  <span class="page-no">Page 02</span>
  <span class="agenda-bar"></span>
</section>

<!-- About -->
<section class="slide slide--about">
  <div class="photo about-photo" style="background:linear-gradient(170deg,#c9b59c,#8c7a68 45%,#3e4a5a)" role="img" aria-label="Photo of a team of colleagues gathered around a computer in an office"></div>
  <span class="heading-rule" style="left:232px;top:10px"></span>
  <h2 class="abs heading about-title">About Us</h2>
  <p class="abs about-lead">TRAVOLIN is a one-stop destination for all your IT Management Requirements. We are committed to delivering cutting-edge, simplified IT solutions through our highly skilled team and flexible engagement models. Whether you need support for integration or ongoing operational services, TRAVOLIN has the insight and technical capability to deliver simplified solutions.</p>
  <div class="abs about-body">
    <p>Our passion, enthusiasm, and value are what make us different from our peers. While there are many businesses providing the same services, what we deliver is unparalleled. Whether services or solutions, we keep standing with our clients through thick and thin.</p>
    <p>Whether you need support for integration or ongoing operational services, TRAVOLIN has the insight and technical capability to deliver simplified solutions.</p>
    <p>Being an Australian based organization, we are 100% Customer Focused and provide innovative and flexible IT services and simple solutions that enhance business productivity. We pride ourselves on the flexibility in our approach.</p>
  </div>
  <span class="copyright">Copyright 2024. All rights reserved.</span>
  <span class="page-no">Page 03</span>
  <span class="foot-bar"></span>
</section>

<!-- Services -->
<section class="slide slide--services">
  <span class="heading-rule" style="left:223px;top:14px"></span>
  <h2 class="abs heading services-title">Our Services</h2>
  <svg class="abs" width="514" height="288" viewBox="0 0 514 288" style="left:0;top:0">
    <defs>
      <filter id="lift" x="-40%" y="-40%" width="180%" height="180%"><feDropShadow dx="0" dy="2" stdDeviation="2.5" flood-color="#000" flood-opacity=".18"/></filter>
    </defs>
    <g fill="none" stroke="#555" stroke-width=".7">
      <polyline points="143,61 196,61 210,79"/>
      <polyline points="143,136 179,136"/>
      <polyline points="143,213 196,213 210,195"/>
      <polyline points="358,61 301,61 289,79"/>
      <polyline points="358,136 320,136"/>
      <polyline points="358,213 301,213 289,195"/>
    </g>
    <g fill="#333">
      <circle cx="143" cy="61" r="1.8"/><circle cx="210" cy="79" r="1.8"/>
      <circle cx="143" cy="136" r="1.8"/><circle cx="179" cy="136" r="1.8"/>
      <circle cx="143" cy="213" r="1.8"/><circle cx="210" cy="195" r="1.8"/>
      <circle cx="358" cy="61" r="1.8"/><circle cx="289" cy="79" r="1.8"/>
      <circle cx="358" cy="136" r="1.8"/><circle cx="320" cy="136" r="1.8"/>
      <circle cx="358" cy="213" r="1.8"/><circle cx="289" cy="195" r="1.8"/>
    </g>
    <circle cx="250" cy="136" r="67" fill="none" stroke="#5ec6e0" stroke-width=".8"/>
    <circle cx="250" cy="136" r="62" fill="none" stroke="var(--blue)" stroke-width="3"/>
    <circle cx="250" cy="136" r="58.5" fill="none" stroke="var(--navy)" stroke-width="2"/>
    <circle cx="250" cy="136" r="55" fill="#fafafa" filter="url(#lift)"/>
    <text x="250" y="144" text-anchor="middle" font-family="Poppins, sans-serif" font-weight="300" font-size="23" fill="var(--blue)" letter-spacing="1">travolin</text>
    <g filter="url(#lift)" fill="#fafafa">
      <circle cx="112" cy="61" r="24"/><circle cx="112" cy="136" r="24"/><circle cx="112" cy="213" r="24"/>
      <circle cx="388" cy="61" r="24"/><circle cx="388" cy="136" r="24"/><circle cx="388" cy="213" r="24"/>
    </g>
    <g fill="none" stroke="#333" stroke-width="1">
      <circle cx="112" cy="61" r="9"/><ellipse cx="112" cy="61" rx="4" ry="9"/><line x1="103" y1="61" x2="121" y2="61"/>
      <rect x="102" y="126" width="20" height="20" rx="3"/><rect x="105" y="129" width="14" height="14" rx="2"/>
      <path d="M101 213 l6 -5 h5 l5 4 l6 -4 v8 l-6 5 l-6 -4 z"/>
      <rect x="381" y="51" width="13" height="18" rx="1"/><line x1="384" y1="56" x2="391" y2="56"/><line x1="384" y1="60" x2="391" y2="60"/><line x1="384" y1="64" x2="389" y2="64"/><line x1="397" y1="52" x2="388" y2="66"/>
      <rect x="380" y="127" width="13" height="18" rx="1"/><rect x="383" y="125" width="7" height="3"/><circle cx="395" cy="143" r="4.5"/><line x1="383" y1="133" x2="390" y2="133"/><line x1="383" y1="137" x2="388" y2="137"/>
      <rect x="378" y="204" width="5" height="4"/><rect x="378" y="211" width="5" height="4"/><rect x="378" y="218" width="5" height="4"/>
      <line x1="386" y1="206" x2="398" y2="206"/><line x1="386" y1="213" x2="398" y2="213"/><line x1="386" y1="220" x2="398" y2="220"/>
    </g>
  </svg>

  <div class="svc-left" style="top:32px"><div class="svc-name">Security Operations<br>Center</div><div class="svc-desc">Single point of contact for incident and service request handling &amp; remote support including a fixed monthly rate with unlimited support under service level agreements through global coverage</div></div>
  <div class="svc-left" style="top:118px"><div class="svc-name">Project Services</div><div class="svc-desc">Provide secured and high-quality service for ad hoc or multi-site project works with on time deliverables</div></div>
  <div class="svc-left" style="top:194px;left:0;width:84px"><div class="svc-name">Procurement Services</div><div class="svc-desc" style="margin-top:8px">The procurement team is specialized in sourcing and supplying products and license to meet our customer's needs. All products we sell are sourced from vendors.</div></div>

  <div class="svc-right" style="top:43px"><div class="svc-name">Service Desk</div><div class="svc-desc">Single point of contact for incident and service request handling &amp; remote support including a fixed monthly rate with unlimited support under service level agreements through global coverage</div></div>
  <div class="svc-right" style="top:119px"><div class="svc-name">Software Development</div><div class="svc-desc">Design unique software as per your business requirement, provide reliable total hosting service by using managed host platforms</div></div>
  <div class="svc-right" style="top:188px"><div class="svc-name">Network Operations Center</div><div class="svc-desc">Monitor each device that connected to network in 24 x 7 and maintain the high level of availability of services</div></div>

  <div class="abs svc-ai"><div class="svc-name">AI as a Service</div><div class="svc-desc" style="margin-top:2px">Artificial Intelligence (AI) can reduce the number of hours your business spends on managing your IT operations. AI has the capabilities to debug issues in large scale deployments much faster and predict anomalies. AI has the capability to fast forward innovations in your business.</div></div>

  <span class="copyright">Copyright 2024. All rights reserved.</span>
  <span class="page-no">Page 04</span>
  <span class="foot-bar"></span>
</section>

<!-- Partners -->
<section class="slide slide--partners">
  <span class="heading-rule" style="left:223px;top:14px"></span>
  <h2 class="abs heading partners-title">Our Partners</h2>
  <div aria-label="Technology partner badges">
    <span class="badge" style="left:13px;top:61px;width:56px"></span>
    <span class="badge" style="left:88px;top:61px;width:100px"></span>
    <span class="badge" style="left:220px;top:63px;width:34px;height:12px"></span>
    <span class="badge" style="left:296px;top:61px;width:36px"></span>
    <span class="badge" style="left:358px;top:63px;width:42px;height:12px"></span>
    <span class="badge" style="left:434px;top:61px;width:58px"></span>

    <span class="badge" style="left:20px;top:110px;width:34px;height:18px"></span>
    <span class="badge" style="left:109px;top:112px;width:60px"></span>
    <span class="badge" style="left:214px;top:109px;width:46px;height:20px"></span>
    <span class="badge" style="left:296px;top:115px;width:30px;height:8px"></span>
    <span class="badge" style="left:361px;top:110px;width:50px;height:18px"></span>
    <span class="badge" style="left:434px;top:110px;width:68px;height:18px"></span>

    <span class="badge" style="left:11px;top:150px;width:42px;height:18px;background:#9cc39a"></span>
    <span class="badge" style="left:99px;top:152px;width:80px;height:18px"></span>
    <span class="badge" style="left:209px;top:154px;width:56px;height:14px"></span>
    <span class="badge" style="left:290px;top:154px;width:42px;height:16px"></span>
    <span class="badge" style="left:358px;top:150px;width:50px;height:18px"></span>
    <span class="badge" style="left:442px;top:154px;width:42px;height:12px"></span>

    <span class="badge" style="left:14px;top:199px;width:40px;height:16px"></span>
    <span class="badge" style="left:102px;top:198px;width:76px;height:18px"></span>
    <span class="badge" style="left:218px;top:200px;width:42px;height:16px"></span>
    <span class="badge" style="left:290px;top:202px;width:40px;height:12px"></span>
    <span class="badge" style="left:357px;top:198px;width:51px;height:18px;background:#e0262b"></span>
    <span class="badge" style="left:451px;top:197px;width:30px;height:18px"></span>

    <span class="badge" style="left:203px;top:242px;width:68px;height:17px"></span>
  </div>
  <span class="copyright">Copyright 2024. All rights reserved.</span>
  <span class="page-no">Page 05</span>
  <span class="foot-bar"></span>
</section>

<!-- Contact -->
<section class="slide slide--contact">
  <svg width="0" height="0" style="position:absolute">
    <defs>
      <symbol id="pin" viewBox="0 0 16 16"><circle cx="8" cy="8" r="7.3" fill="#fff" stroke="var(--blue)" stroke-width="1"/><path d="M8 3.6a2.9 2.9 0 0 0-2.9 2.9c0 2.2 2.9 5.6 2.9 5.6s2.9-3.4 2.9-5.6A2.9 2.9 0 0 0 8 3.6z" fill="var(--blue)"/><circle cx="8" cy="6.5" r="1.1" fill="#fff"/></symbol>
      <symbol id="pin-solid" viewBox="0 0 16 16"><circle cx="8" cy="8" r="8" fill="var(--blue)"/><path d="M8 3.6a2.9 2.9 0 0 0-2.9 2.9c0 2.2 2.9 5.6 2.9 5.6s2.9-3.4 2.9-5.6A2.9 2.9 0 0 0 8 3.6z" fill="#fff"/><circle cx="8" cy="6.5" r="1.1" fill="var(--blue)"/></symbol>
    </defs>
  </svg>
  <div class="abs wordmark contact-brand">travolin</div>
  <div class="abs contact-thanks">Thank You</div>
  <div class="abs contact-line" style="top:110px">
    <svg width="16" height="16" viewBox="0 0 16 16"><circle cx="8" cy="8" r="8" fill="var(--blue)"/><rect x="4" y="5.2" width="8" height="5.6" rx=".8" fill="#fff"/><polyline points="4.3,5.6 8,8.4 11.7,5.6" fill="none" stroke="var(--blue)" stroke-width=".8"/></svg>
    <span>connect@travolin.com.au</span>
  </div>
  <div class="abs contact-line" style="top:140px">
    <svg width="16" height="16" viewBox="0 0 16 16"><circle cx="8" cy="8" r="8" fill="var(--blue)"/><path d="M5.2 4.2l1.6-.4 1 2.2-1 .8a5 5 0 0 0 2.4 2.4l.8-1 2.2 1-.4 1.6c-3.9.3-6.9-2.7-6.6-6.6z" fill="#fff"/></svg>
    <span>+61 (02) 8123 4567</span>
  </div>

  <div class="abs" style="left:35px;top:176px">
    <div class="office-head"><svg width="16" height="16"><use href="#pin-solid"/></svg>AUSTRALIA</div>
    <div class="office-body" style="margin-left:24px">TRAVOLIN PTY LIMITED<br>www.travolin.com.au<br>ABN 41 572 309 118<br>PO BOX 742 NORTH BAY<br>2088 NSW<br>AUSTRALIA</div>
  </div>
  <div class="abs" style="left:232px;top:37px">
    <div class="office-head"><svg width="14" height="14"><use href="#pin"/></svg>USA</div>
    <div class="office-body">TRAVOLIN PTY LIMITED<br>www.travolin.com.au<br>ABN 41 572 309 118<br>1840 Harbor Ridge Drive<br>Lakeview, MI 48211<br>USA</div>
  </div>
  <div class="abs" style="left:345px;top:37px">
    <div class="office-head"><svg width="14" height="14"><use href="#pin"/></svg>SRI LANKA</div>
    <div class="office-body">TRAVOLIN ASIA PACIFIC (PRIVATE) LIMITED<br>www.travolin.lk<br>(PV 00387204)<br>14/2/4B, ORCHARD TOWER 3RD FLOOR<br>LOTUS ROAD<br>00300, COLOMBO<br>SRI LANKA</div>
  </div>
  <div class="abs" style="left:232px;top:176px">
    <div class="office-head"><svg width="14" height="14"><use href="#pin"/></svg>NEW ZEALAND</div>
    <div class="office-body">TRAVOLIN NZ PTY LIMITED<br>NZBN 942 117 5038 261<br>22/61 KEMPTON ROAD<br>Riverside<br>Hamilton NZ 3204<br>NEW ZEALAND</div>
  </div>
  <div class="abs" style="left:345px;top:176px">
    <div class="office-head"><svg width="14" height="14"><use href="#pin"/></svg>SINGAPORE</div>
    <div class="office-body">TRAVOLIN PTY LIMITED<br>www.travolin.com.au<br>ABN 41 572 309 118<br>PO BOX 742 NORTH BAY<br>2088 NSW<br>SINGAPORE</div>
  </div>
</section>

</body>
</html>
```